Q&J RESTORATION

I want a brochure similiar to the example i've attached.
My company name is Q&J Restoration. The website is: Q-J-Restoration.example.
The phone number is 919.555.0147.

I don't like the "yellow" being the main color of the example so I'm open to suggestions. I want something CLEAN & Simple, like our logo . This will be a bi fold brochure

```html
<!DOCTYPE html>
<html lang="en">
<head>
<meta charset="utf-8">
<title>Q&amp;J Restoration – Bi-fold Brochure</title>
<link href="https://fonts.googleapis.com/css2?family=Poppins:wght@400;500;600&display=swap" rel="stylesheet">
<style>
  :root {
    --page-bg: #e3e3e3;
    --paper-light: #efefef;
    --charcoal: #3a3a3a;
    --charcoal-deep: #2c2c2c;
    --charcoal-soft: #4b4b4b;
    --brand-green: #6aab1f;
    --photo-green-light: #9ad443;
    --photo-green-dark: #4d8710;
    --text-white: #ffffff;
    --text-dark: #1e1e1e;
  }
  * { box-sizing: border-box; margin: 0; padding: 0; }
  html, body {
    width: 1200px; height: 800px; overflow: hidden;
    background: var(--page-bg);
    font-family: "Poppins", sans-serif;
  }
  .spread {
    position: absolute; left: 135px; top: 40px;
    width: 930px; height: 720px;
    background: var(--paper-light);
    box-shadow: 0 12px 30px rgba(0,0,0,.18);
    overflow: hidden;
  }
  .spread-shapes { position: absolute; inset: 0; }

  .brand-name {
    position: absolute;
    display: flex; align-items: center; gap: 10px;
    font-weight: 500; letter-spacing: .02em; white-space: nowrap;
  }
  .brand-name .brand-square { width: 12px; height: 12px; flex: none; }

  /* back cover (left panel) */
  .back-brand { left: 120px; top: 300px; font-size: 30px; color: var(--text-white); }
  .back-brand .brand-square { background: var(--text-white); }

  .back-contact { position: absolute; left: 56px; top: 470px; color: var(--text-white); }
  .back-question { font-size: 19px; font-weight: 500; letter-spacing: .01em; }
  .back-tagline { font-size: 19px; font-weight: 500; color: var(--brand-green); margin-bottom: 14px; }
  .contact-line {
    display: flex; align-items: center; gap: 8px;
    font-size: 15px; font-weight: 400; margin-bottom: 6px;
  }
  .contact-line svg { width: 15px; height: 15px; flex: none; }

  /* front cover (right panel) */
  .front-brand {
    left: 718px; top: 64px; font-size: 19px; color: var(--text-dark);
  }
  .front-brand .brand-square { width: 10px; height: 10px; background: var(--text-dark); }

  .front-headline {
    position: absolute; left: 770px; top: 280px;
    transform: translate(-50%, -50%) rotate(47.8deg);
    color: var(--text-white); font-weight: 600; text-transform: uppercase;
    line-height: .95; text-align: left; white-space: nowrap;
  }
  .front-headline .headline-small { display: block; font-size: 36px; letter-spacing: .02em; }
  .front-headline .headline-large { display: block; font-size: 66px; letter-spacing: .01em; }

  .front-web {
    position: absolute; left: 640px; top: 662px;
    color: var(--text-dark); font-size: 16px; font-weight: 500;
  }
</style>
</head>
<body>
  <main class="spread">
    <svg class="spread-shapes" viewBox="0 0 930 720" width="930" height="720">
      <defs>
        <linearGradient id="blueprint-tone" x1="0" y1="0" x2="1" y2="1">
          <stop offset="0" stop-color="#4b4b4b"/>
          <stop offset=".55" stop-color="#3a3a3a"/>
          <stop offset="1" stop-color="#2c2c2c"/>
        </linearGradient>
        <linearGradient id="renovation-tone" x1="0" y1="0" x2="1" y2="1">
          <stop offset="0" stop-color="#9ad443"/>
          <stop offset="1" stop-color="#4d8710"/>
        </linearGradient>
      </defs>
      <polygon class="blueprint-photo" role="img" aria-label="Photo of rolled architectural blueprints"
               points="90,0 640,0 180,720 0,720 0,75" fill="url(#blueprint-tone)"/>
      <polygon class="renovation-photo" role="img" aria-label="Green-toned photo of a kitchen under renovation with a ladder"
               points="535,164 723,371 500,720 180,720" fill="url(#renovation-tone)"/>
      <polygon class="headline-band" points="640,0 930,320 930,600 535,164" fill="#6aab1f"/>
    </svg>

    <!-- back cover -->
    <div class="brand-name back-brand"><span class="brand-square"></span>Q&amp;J Restoration</div>

    <div class="back-contact">
      <p class="back-question">INSURANCE CLAIM?</p>
      <p class="back-tagline">WE'RE ON YOUR TEAM.</p>
      <p class="contact-line">
        <svg viewBox="0 0 16 16"><circle cx="8" cy="8" r="7" fill="none" stroke="#6aab1f" stroke-width="1.6"/><path d="M1 8h14M8 1c3 3 3 11 0 14M8 1c-3 3-3 11 0 14" fill="none" stroke="#6aab1f" stroke-width="1.2"/></svg>
        Q-J-Restoration.example
      </p>
      <p class="contact-line">
        <svg viewBox="0 0 16 16"><path d="M4 1.5l2.3 3-1.4 1.6c.8 1.9 2.2 3.3 4 4.1l1.6-1.4 3 2.3-1.2 2.6C6.8 13.6 2.4 9.2 1.4 2.7z" fill="#6aab1f"/></svg>
        919.555.0147
      </p>
    </div>

    <!-- front cover -->
    <div class="brand-name front-brand"><span class="brand-square"></span>Q&amp;J Restoration</div>

    <h1 class="front-headline">
      <span class="headline-small">Insurance</span>
      <span class="headline-large">Claim</span>
      <span class="headline-small">Specialist</span>
    </h1>

    <p class="contact-line front-web">
      <svg viewBox="0 0 16 16"><circle cx="8" cy="8" r="7" fill="none" stroke="#6aab1f" stroke-width="1.6"/><path d="M1 8h14M8 1c3 3 3 11 0 14M8 1c-3 3-3 11 0 14" fill="none" stroke="#6aab1f" stroke-width="1.2"/></svg>
      Q-J-Restoration.example
    </p>
  </main>
</body>
</html>
```